light box menu and wall graphics

HI My name is Derek Halloway and I am putting together a Pebble Mugs franchise. We are a high quaulity coffee offering and the retail concept is for a in-line store in a busy shopping centre food court. We are a highly visible coffee offering with vibrant bright orange colour (pantone 021 / process m60_y100)
Orange might make a good background on the menu board as it needs to blend in with colour scheme. Also the text has to be at least 15ml and not too busy but clearly legible. The font is: Akzent Rounded
The twin light boxes being used is from http://www.brightpanelstore.example.au/pg/lightboxes/new/sdb/light-box-1560S.aspx
They measure in total 3m wide X .6 height

There are two elements to this job, one is the twin menu boards and the other is the wall graphic.
please see wall graphic examples attached.
This graphic is to be painted onto the wall by a sign writter.
The design to go on the wall needs to be a synonymous with our quality coffee vison and match the shop design, I have examples of the type of wall art I am after attached. I was thinking somehow a Cart with wings would look neat and we could incorportate some text into it. Such as "Coffee with Substance makes you feel good" and "Original Cart" Flames could look amazing too!

My website is unfortunately down at the moment but I am attaching plenty

I have just added the menu in easy to read updated format.
Thanks to those who have expressed interest!
Updates

Hi Designers, I have just increased first prize by $100.00

Please note the signage boards run horizontally not vertically.  I have also added more artwork.

thanks

Derek

 HI there, thanks for joining.  I have just updated the brief to make it as clear as possible.

Hope you enjoy this experience.  I am here to answer any questions.

Derek

Thank you for accepting my invitation for this design job.

Look forward to seeing some designs as per brief.

Need to have this finished by Friday the 19th of October.  Thanks

Target Market(s)

Coffee lovers, kids who want hot chocolates, frappes,
etc

Industry/Entity Type

Shopping

Requirements
Must have
• Must have coffee in it for clarity.
Also in the menu any images of food or drink must be photo/posters attached

```html
<!DOCTYPE html>
<html lang="en">
<head>
<meta charset="utf-8">
<title>Pebble Mugs – Tea &amp; Kids Menu Board</title>
<link rel="stylesheet" href="https://fonts.googleapis.com/css2?family=Nunito:wght@800;900&display=swap">
<style>
  :root {
    --orange: #ef7d00;
    --ink: #231f20;
    --white: #ffffff;
    --frame: #bcbdc0;
    --backdrop-light: #ffffff;
    --backdrop-edge: #e4e4e5;
  }
  * { margin: 0; padding: 0; box-sizing: border-box; }
  html, body { width: 1200px; height: 1000px; overflow: hidden; }
  body {
    position: relative;
    font-family: "Nunito", "Arial Rounded MT Bold", sans-serif;
    font-weight: 800;
    background: radial-gradient(ellipse at 50% 50%, var(--backdrop-light) 40%, var(--backdrop-edge) 100%);
  }
  .frame-band {
    position: absolute; left: 0; top: 186px; width: 1200px; height: 626px;
    background: var(--frame);
  }
  .menu-board {
    position: absolute; left: 27px; top: 213px; width: 1146px; height: 573px;
    background: var(--orange);
  }
  .menu-header {
    position: absolute; left: 0; top: 0; width: 100%; height: 96px;
    background: var(--white);
  }
  .section-title {
    position: absolute; top: 33px;
    font-size: 42px; font-weight: 900; color: var(--orange);
    letter-spacing: -0.5px; line-height: 1;
  }
  .section-title--tea { left: 30px; }
  .section-title--kids { left: 604px; }

  .size-prices {
    position: absolute; top: 40px; display: flex; align-items: baseline; gap: 18px;
    line-height: 1; white-space: nowrap;
  }
  .size-prices--tea { left: 249px; }
  .size-prices--kids { left: 932px; }
  .size-price { display: flex; align-items: baseline; }
  .size-label { font-size: 28px; font-weight: 900; color: var(--ink); margin-right: 7px; }
  .currency { font-size: 16px; color: var(--ink); }
  .price-main { font-size: 25px; color: var(--orange); }
  .price-cents { font-size: 17px; color: var(--orange); }

  .item-list { position: absolute; top: 113px; list-style: none; }
  .item-list--tea { left: 30px; }
  .item-list--kids { left: 604px; }
  .menu-item {
    height: 41px; font-size: 27px; color: var(--ink);
    letter-spacing: -0.3px; line-height: 1; white-space: nowrap;
    display: flex; align-items: baseline;
  }
  .item-name { display: inline-block; }
  .item-price {
    position: absolute; left: 248px; display: flex; align-items: baseline; color: var(--white);
  }
  .item-price .currency { font-size: 16px; color: var(--white); }
  .item-price .price-main { font-size: 25px; color: var(--white); }
  .item-price .price-cents { font-size: 17px; color: var(--white); }

  .brand-mark {
    position: absolute; left: 674px; top: 395px; width: 370px;
    display: flex; align-items: center; justify-content: center; gap: 16px;
  }
  .brand-square { width: 30px; height: 30px; background: var(--ink); flex: none; }
  .brand-name {
    font-size: 56px; font-weight: 900; color: var(--ink);
    letter-spacing: -1px; line-height: 1; white-space: nowrap;
  }
</style>
</head>
<body>
  <div class="frame-band"></div>
  <main class="menu-board">
    <header class="menu-header">
      <h2 class="section-title section-title--tea">Tea</h2>
      <div class="size-prices size-prices--tea">
        <span class="size-price"><span class="size-label">S</span><span class="currency">$</span><span class="price-main">3</span><span class="price-cents">.80</span></span>
        <span class="size-price"><span class="size-label">M</span><span class="currency">$</span><span class="price-main">4</span><span class="price-cents">.50</span></span>
        <span class="size-price"><span class="size-label">L</span><span class="currency">$</span><span class="price-main">4</span><span class="price-cents">.90</span></span>
      </div>
      <h2 class="section-title section-title--kids">Kids</h2>
      <div class="size-prices size-prices--kids">
        <span class="size-price"><span class="size-label">S</span><span class="currency">$</span><span class="price-main">3</span><span class="price-cents">.00</span></span>
      </div>
    </header>

    <ul class="item-list item-list--tea">
      <li class="menu-item">English Breakfast</li>
      <li class="menu-item">Chamomile Flowers</li>
      <li class="menu-item">Earl Grey Lavender</li>
      <li class="menu-item">Ginger Peach</li>
      <li class="menu-item">Rooibos Caramel</li>
      <li class="menu-item">Hindu Chai</li>
      <li class="menu-item">Japanese Sencha</li>
      <li class="menu-item">African Cocoa</li>
      <li class="menu-item">Wild Berry</li>
      <li class="menu-item">Organic Peppermint</li>
    </ul>

    <ul class="item-list item-list--kids">
      <li class="menu-item">Warm Chocolate</li>
      <li class="menu-item">Cool Chocolate</li>
      <li class="menu-item"><span class="item-name">Babycino Mini</span><span class="item-price"><span class="currency">$</span><span class="price-main">1</span><span class="price-cents">.00</span></span></li>
      <li class="menu-item"><span class="item-name">Babycino Grande</span><span class="item-price"><span class="currency">$</span><span class="price-main">2</span><span class="price-cents">.50</span></span></li>
    </ul>

    <div class="brand-mark">
      <span class="brand-square"></span>
      <span class="brand-name">Pebble Mugs</span>
    </div>
  </main>
</body>
</html>
```